Accounting firm needing business card / letterhead designed
Marcus L. Trenholm, CPA
marcus@veltrowledger.com
www.veltrowledger.com
842 E Alder Ave Perrysburg, OH 43827
419-562-0974

```html
<!DOCTYPE html>
<html lang="en">
<head>
<meta charset="utf-8">
<title>Veltro Ledger – Business Card</title>
<link href="https://fonts.googleapis.com/css2?family=Barlow+Semi+Condensed:wght@600;700&family=Open+Sans:wght@400&display=swap" rel="stylesheet">
<style>
  :root {
    --backdrop: #e6e6e6;
    --navy: #22134a;
    --green: #5cb531;
    --ink: #1f1f24;
    --card-white: #f7f7f7;
  }
  * { margin: 0; padding: 0; box-sizing: border-box; }
  html, body { width: 1200px; height: 576px; overflow: hidden; }
  body { background: var(--backdrop); position: relative; font-family: "Open Sans", Arial, sans-serif; }

  .card {
    position: absolute;
    border-radius: 16px;
    box-shadow: 0 3px 8px rgba(0,0,0,0.18);
  }
  .card-front {
    left: 82px; top: 138px; width: 484px; height: 294px;
    background: var(--navy);
    display: flex; align-items: center; justify-content: center;
  }
  .front-wordmark {
    font-family: "Barlow Semi Condensed", Arial, sans-serif;
    font-weight: 700;
    font-size: 52px;
    letter-spacing: 2px;
    text-transform: uppercase;
    color: #ffffff;
    line-height: 1;
  }
  .card-back {
    left: 602px; top: 138px; width: 481px; height: 292px;
    background: var(--card-white);
  }
  .holder-name {
    position: absolute; left: 23px; top: 32px;
    font-family: "Barlow Semi Condensed", Arial, sans-serif;
    font-weight: 700; font-size: 20px; color: var(--navy);
  }
  .holder-title {
    position: absolute; left: 23px; top: 59px;
    font-size: 11.5px; color: var(--green);
  }
  .address {
    position: absolute; left: 23px; top: 172px;
    font-size: 12.5px; line-height: 18px; color: var(--ink);
  }
  .contact-list {
    position: absolute; left: 23px; top: 214px;
    list-style: none; font-size: 12.5px; color: var(--ink);
  }
  .contact-list li { display: flex; align-items: center; height: 18px; }
  .contact-list svg { width: 11px; height: 11px; margin-right: 12px; fill: var(--green); }
  .back-wordmark {
    position: absolute; right: 28px; top: 211px;
    font-family: "Barlow Semi Condensed", Arial, sans-serif;
    font-weight: 700; font-size: 34px; letter-spacing: 1px;
    text-transform: uppercase; color: var(--navy); line-height: 1;
  }
</style>
</head>
<body>
  <section class="card card-front">
    <div class="front-wordmark">Veltro Ledger</div>
  </section>

  <section class="card card-back">
    <h1 class="holder-name">Marcus L. Trenholm, CPA</h1>
    <p class="holder-title">Director</p>
    <p class="address">842 E Alder Ave<br>Perrysburg, OH 43827</p>
    <ul class="contact-list">
      <li>
        <svg viewBox="0 0 12 12" aria-hidden="true"><path d="M1 4c0-1.5 2-2.5 5-2.5S11 2.5 11 4v1H8.5V3.8h-5V5H1z"/><rect x="2" y="6" width="8" height="5" rx="1"/></svg>
        419-562-0974
      </li>
      <li>
        <svg viewBox="0 0 12 12" aria-hidden="true"><path d="M0 2h12v8H0z M1 3l5 4 5-4" stroke="#f7f7f7" stroke-width="0.8"/></svg>
        marcus@veltrowledger.com
      </li>
      <li>
        <svg viewBox="0 0 12 12" aria-hidden="true"><circle cx="6" cy="6" r="5.5"/><path d="M0.5 6h11M6 0.5v11M2 3h8M2 9h8" stroke="#f7f7f7" stroke-width="0.7" fill="none"/></svg>
        www.veltrowledger.com
      </li>
    </ul>
    <div class="back-wordmark">Veltro Ledger</div>
  </section>
</body>
</html>
```